LEARN Business Skills so you can Earn a good living

size of the poster is 8”x 10.75" plus 0.25" bleed.
Please leave 1 inch on the bottoum for footer
I want a design a poster that will attract people's attention.
I appreciate a creative ad however the ad should not take away from being able to clearly read the text.
-I also appreciate a simple creative ad that is not too busy.
-you can use graphics, vectors, or pictures of real people.
-however, if you use real people it should be a white male that is wearing a white shirt and look like a professional person.

Target Market(s)

Potential young business people

Industry/Entity Type

education

Requirements
Must have
• easy to read the text
Nice to have
• I would like a "creative" simple ad that is easy to be read
Should not have
• pictures of women

```html
<!DOCTYPE html>
<html lang="en">
<head>
<meta charset="utf-8">
<title>Learn to Earn – Business Enrichment Course</title>
<link rel="stylesheet" href="https://fonts.googleapis.com/css2?family=Playfair+Display:wght@900&family=Poppins:wght@700&family=Roboto:wght@400;500&display=swap">
<style>
  :root {
    --paper: #f7fafb;
    --ink: #0d0d0d;
    --text: #1c1c1c;
    --accent: #c8202f;
    --hero-top: #ececec;
    --hero-mid: #ddd2b0;
    --hero-low: #c9a24a;
  }
  * { margin: 0; padding: 0; box-sizing: border-box; }
  html, body { width: 895px; height: 1200px; overflow: hidden; background: var(--paper); }
  .poster {
    position: relative;
    width: 895px;
    height: 1200px;
    background: var(--paper);
    font-family: "Roboto", Arial, sans-serif;
    color: var(--text);
  }
  .headline {
    position: absolute;
    top: 76px;
    left: 0;
    width: 100%;
    text-align: center;
    font-family: "Poppins", Arial, sans-serif;
    font-weight: 700;
    font-size: 98px;
    letter-spacing: -1px;
    line-height: 1.2;
    color: var(--ink);
  }
  .hero-art {
    position: absolute;
    left: 82px;
    top: 202px;
    width: 731px;
    height: 530px;
    border-radius: 14px;
    background: linear-gradient(180deg, var(--hero-top) 0%, var(--hero-mid) 55%, var(--hero-low) 100%);
  }
  .course-title {
    position: absolute;
    top: 752px;
    left: 0;
    width: 100%;
    text-align: center;
    font-weight: 500;
    font-size: 31px;
    color: var(--accent);
  }
  .tagline {
    position: absolute;
    top: 790px;
    left: 0;
    width: 100%;
    text-align: center;
    font-weight: 500;
    font-size: 29px;
    color: var(--ink);
  }
  .quote-mark {
    position: absolute;
    font-family: "Playfair Display", Georgia, serif;
    font-weight: 900;
    font-size: 118px;
    line-height: 1;
    color: var(--accent);
  }
  .quote-open { left: 106px; top: 772px; }
  .quote-close { left: 733px; top: 772px; }
  .benefits {
    position: absolute;
    top: 863px;
    left: 0;
    width: 100%;
    text-align: center;
    font-weight: 500;
    font-size: 20.5px;
    color: var(--ink);
  }
  .benefits .sep { margin: 0 9px; }
  .divider {
    position: absolute;
    top: 931px;
    left: 379px;
    width: 138px;
    height: 2px;
    background: var(--ink);
  }
  .topics {
    position: absolute;
    top: 976px;
    list-style: none;
    font-size: 15.5px;
    line-height: 19.4px;
    color: var(--text);
  }
  .topics li { position: relative; padding-left: 13px; white-space: nowrap; }
  .topics li::before {
    content: "";
    position: absolute;
    left: 0;
    top: 7px;
    width: 5px;
    height: 5px;
    border-radius: 50%;
    background: var(--accent);
  }
  .topics li.no-bullet::before { display: none; }
  .topics-1 { left: 65px; }
  .topics-2 { left: 322px; }
  .topics-3 { left: 517px; }
  .topics-4 { left: 725px; }
</style>
</head>
<body>
<main class="poster">
  <h1 class="headline">Learn to Earn</h1>

  <div class="hero-art" role="img" aria-label="Photo of a small businessman figurine sitting on a stack of gold and silver coins over a soft grey dot pattern"></div>

  <h2 class="course-title">Business Enrichment Course</h2>
  <span class="quote-mark quote-open" aria-hidden="true">“</span>
  <p class="tagline">A proven success of helping people</p>
  <span class="quote-mark quote-close" aria-hidden="true">”</span>

  <p class="benefits">Get A Quality Job<span class="sep">|</span>Start/grow Your Business<span class="sep">|</span>Increase Your Salary</p>

  <div class="divider"></div>

  <ul class="topics topics-1">
    <li>Business Admnistration</li>
    <li>Small&nbsp; Business Management</li>
    <li>Finance</li>
    <li>Investments</li>
    <li>Computers</li>
    <li>Accounting</li>
  </ul>
  <ul class="topics topics-2">
    <li>Sales</li>
    <li>Marketing</li>
    <li>Project Management</li>
    <li class="no-bullet">Interviewing Skills</li>
    <li>Business Law</li>
    <li>Negotiation</li>
  </ul>
  <ul class="topics topics-3">
    <li>Public Speaking</li>
    <li>Import/export</li>
    <li>Information Technoloy</li>
    <li>Distribution</li>
    <li>Marketing</li>
    <li>LedgerPro</li>
  </ul>
  <ul class="topics topics-4">
    <li>Real Estate</li>
    <li>Health Care</li>
    <li>Management</li>
    <li>Shopwell</li>
  </ul>
</main>
</body>
</html>
```